PowerPoint Listing Presentation for Real Estate Agency

We need a PowerPoint presentation for a new real estate brokerage team.

[[[[[[submit 1-3 sample slides for review - i will provide feedback and you can make changes if you want to - we will not be deciding on a design prior to the deadline]]]]]

******ATTN: DESIGNERS, if your skills are webdesign then just look at this like a portable website or a brochure. it should be easy enough******

NOTE: we have all the data to put into the slides. You just need to come up with the design and layout. we have a sample design that we like and have provided.

This focus will be for the home listing side of the business (a presentation for home sellers to convince them to use our services). The data and slides will present our team and the benefits, in the best light, to use our services over that of other real estate agent applying for the job. This presentation will proved facts and benefits and describe our special and unique offerings that will show a home seller why we can sell their home for more money in less time and with the least amount of hassle. The main color scheme is Dark Blue and White (we want some additional colors included - based on your creativity. otherwise the presentation will too monotone). We would like to see the use of Statistical Graphs (3-D) - data provided. We have photos of our team and a new logo (the logo could have some minor adjustment to clean it up if necessary) - also uploaded. We have about 80-90% of the information that will be put into the slides and will need to work closely to get the design and data integrated into the presentation (should be easier then it sounds). We should be able to add slides and data 'at will' over time via our master slides built into the presentation. We have a pretty good sample presentation that we like and can be used as a guideline (this is from our affiliated business network and we have full rights to all the information), it is uploaded but doesn't contain all the slide because of size limitations.

NOTE: An additional buyers presentation will be needed after we get the sellers presentation completed, which means additional work.

This should be enough to get you started and we are available if you have any questions to help you with the project. there will be around 60-70 total slides. once concept is completed it will be easy to create the slides.

Target Market(s)

home sellers. people who are moving to a new and better home or relocation for job reasons. typically more established in life

Industry/Entity Type

Real Estate

Requirements
Must have
• all the slides must be congruent. in other words, the exact same layout feel should used across the board. we are working on building our trade dress/image. Also, it must have a soft and inviting overall feel, yet show strength of ability.
Nice to have
• nice to have use of real people images when necessary. 3D graphs would be nice. clean modern look and feel, yet sophisticated and professional.
Should not have
• should not have a lot of time consuming transitions. do not include 3D stick figures or distracting moving gifs

```html
<!DOCTYPE html>
<html lang="en">
<head>
<meta charset="utf-8">
<title>Our Client Testimonials</title>
<link href="https://fonts.googleapis.com/css2?family=Tinos:wght@400;700&display=swap" rel="stylesheet">
<style>
  :root {
    --navy: #0b2c5e;
    --navy-deep: #082552;
    --accent-blue: #2f7fe0;
    --band-blue: #5b8fdc;
    --gold: #f6b51c;
    --bubble-line: #6d9ad8;
    --sky-top: #ffffff;
    --sky-bottom: #c9dcf3;
    --ghost: rgba(150, 180, 220, 0.28);
  }
  html, body {
    margin: 0;
    padding: 0;
    overflow: hidden;
    background: #ffffff;
  }
  .slide {
    position: relative;
    width: 1200px;
    height: 900px;
    overflow: hidden;
    font-family: "Tinos", "Times New Roman", serif;
    background: linear-gradient(180deg, var(--sky-top) 0%, #eef4fc 40%, var(--sky-bottom) 100%);
  }
  .slide-frame {
    position: absolute;
    inset: 0;
    width: 1200px;
    height: 900px;
  }
  .backdrop-houses {
    position: absolute;
    left: 0;
    top: 300px;
    width: 1060px;
    height: 480px;
    background: radial-gradient(ellipse at 50% 55%, var(--ghost) 0%, rgba(150,180,220,0.12) 55%, rgba(150,180,220,0) 80%);
  }
  .title-row {
    position: absolute;
    left: 592px;
    top: 38px;
    display: flex;
    align-items: center;
    gap: 14px;
  }
  .title-icon {
    width: 64px;
    height: 64px;
  }
  .slide-title {
    margin: 0;
    font-size: 45px;
    font-weight: 400;
    color: var(--navy);
    letter-spacing: 0.2px;
  }
  .slide-subtitle {
    position: absolute;
    left: 0;
    top: 132px;
    width: 1232px;
    margin: 0;
    text-align: center;
    font-size: 28px;
    font-weight: 400;
    color: var(--accent-blue);
  }
  .testimonial {
    position: absolute;
  }
  .testimonial-bubble {
    position: absolute;
    left: 0;
    top: 0;
  }
  .testimonial-quote {
    position: absolute;
    margin: 0;
    left: 0;
    top: 0;
    width: 411px;
    height: 198px;
    box-sizing: border-box;
    padding: 18px 45px 0;
    text-align: center;
    font-size: 22px;
    line-height: 42px;
    color: var(--navy);
  }
  .testimonial-author {
    position: absolute;
    margin: 0;
    white-space: nowrap;
    font-size: 30px;
    color: var(--navy);
    transform: translateX(-50%);
  }
  .testimonial-author .company {
    color: var(--accent-blue);
  }
  .t-one   { left: 162px; top: 183px; }
  .t-two   { left: 657px; top: 183px; }
  .t-three { left: 402px; top: 504px; }
  .t-one .testimonial-author   { left: 132px; top: 262px; }
  .t-two .testimonial-author   { left: 237px; top: 262px; }
  .t-three .testimonial-author { left: 132px; top: 265px; }
  .agency-graphic {
    position: absolute;
    left: 22px;
    top: 800px;
    width: 182px;
    height: 88px;
    background: linear-gradient(180deg, #2a5fa8 0%, var(--navy) 100%);
  }
  .partner-mark {
    position: absolute;
    right: 30px;
    top: 806px;
    display: flex;
    align-items: center;
    gap: 10px;
  }
  .partner-square {
    width: 22px;
    height: 22px;
    background: #ffffff;
  }
  .partner-name {
    font-size: 24px;
    color: #ffffff;
    white-space: nowrap;
  }
</style>
</head>
<body>
<div class="slide">

  <div class="backdrop-houses" role="img" aria-label="Faint background illustration of houses"></div>

  <svg class="slide-frame" viewBox="0 0 1200 900" aria-hidden="true">
    <path d="M0,0 L440,0 C320,50 110,170 0,330 Z" fill="var(--band-blue)"/>
    <path d="M0,0 L426,0 C310,45 100,160 0,312 Z" fill="var(--gold)"/>
    <path d="M0,0 L412,0 C300,40 92,150 0,292 Z" fill="var(--navy-deep)"/>
    <path d="M520,900 C790,800 1050,600 1200,300 L1200,900 Z" fill="var(--band-blue)"/>
    <path d="M545,900 C805,805 1060,610 1200,312 L1200,900 Z" fill="var(--gold)"/>
    <path d="M560,900 C815,810 1068,620 1200,326 L1200,900 Z" fill="var(--navy-deep)"/>
  </svg>

  <header class="title-row">
    <svg class="title-icon" viewBox="0 0 64 64" aria-hidden="true">
      <defs>
        <radialGradient id="icon-glow" cx="40%" cy="30%" r="70%">
          <stop offset="0" stop-color="#3d7fd0"/>
          <stop offset="1" stop-color="#0b2c5e"/>
        </radialGradient>
      </defs>
      <circle cx="32" cy="30" r="28" fill="url(#icon-glow)"/>
      <path d="M18,32 L32,19 L46,32" fill="none" stroke="#ffffff" stroke-width="3" stroke-linejoin="round"/>
      <rect x="22" y="31" width="20" height="13" fill="none" stroke="#ffffff" stroke-width="3"/>
      <rect x="30" y="34" width="6" height="5" fill="#ffffff"/>
    </svg>
    <h1 class="slide-title">Our Client Testimonials...</h1>
  </header>

  <p class="slide-subtitle">Our service, care and results is what keeps our clients coming back</p>

  <section class="testimonial t-one">
    <svg class="testimonial-bubble" width="420" height="270" viewBox="0 0 420 270" aria-hidden="true">
      <path d="M19,1.5 H392 Q409.5,1.5 409.5,19 V180 Q409.5,197.5 392,197.5 H174 L105,257 L129,197.5 H19 Q1.5,197.5 1.5,180 V19 Q1.5,1.5 19,1.5 Z" fill="#ffffff" stroke="var(--bubble-line)" stroke-width="1.5"/>
    </svg>
    <p class="testimonial-quote">Lorem ipsum dolor sit ipsum Lorem ipsum dolor sit ipsum Lorem ipsum dolor sit ipsum Lorem ipsum dolor sit ipsum Lorem</p>
    <p class="testimonial-author">Director Name - <span class="company">Company</span></p>
  </section>

  <section class="testimonial t-two">
    <svg class="testimonial-bubble" width="420" height="270" viewBox="0 0 420 270" aria-hidden="true">
      <path d="M19,1.5 H392 Q409.5,1.5 409.5,19 V180 Q409.5,197.5 392,197.5 H281 L305,257 L236,197.5 H19 Q1.5,197.5 1.5,180 V19 Q1.5,1.5 19,1.5 Z" fill="#ffffff" stroke="var(--bubble-line)" stroke-width="1.5"/>
    </svg>
    <p class="testimonial-quote">Lorem ipsum dolor sit ipsum Lorem ipsum dolor sit ipsum Lorem ipsum dolor sit ipsum Lorem ipsum dolor sit ipsum Lorem</p>
    <p class="testimonial-author">Director Name - <span class="company">Company</span></p>
  </section>

  <section class="testimonial t-three">
    <svg class="testimonial-bubble" width="420" height="270" viewBox="0 0 420 270" aria-hidden="true">
      <path d="M19,1.5 H392 Q409.5,1.5 409.5,19 V180 Q409.5,197.5 392,197.5 H175 L106,257 L130,197.5 H19 Q1.5,197.5 1.5,180 V19 Q1.5,1.5 19,1.5 Z" fill="#ffffff" stroke="var(--bubble-line)" stroke-width="1.5"/>
    </svg>
    <p class="testimonial-quote">Lorem ipsum dolor sit ipsum Lorem ipsum dolor sit ipsum Lorem ipsum dolor sit ipsum Lorem ipsum dolor sit ipsum Lorem</p>
    <p class="testimonial-author">Director Name - <span class="company">Company</span></p>
  </section>

  <div class="agency-graphic" role="img" aria-label="Agency illustration of a row of houses"></div>

  <div class="partner-mark">
    <span class="partner-square"></span>
    <span class="partner-name">Harlow &amp; Finch</span>
  </div>

</div>
</body>
</html>
```